Veltrane Group Business Card Design

The CEO is looking for a new trendy look for his business card.
You can stay with current branding or come up with something new/creative. It can be 3D, including Medical Office buildings. You can use our logo in a variety of colors. Please include name, title, company name, company website, email address, cell number

Target Market(s)

Real Estate Development and Construction

Industry/Entity Type

Health care real estate

Contact Information for Business Card

Rohesh Kamdar, CEO M-604.781.2249 E-roheshkamdar@veltrane.com Address:4180 Lindqvist Ave, Tampa, FL 33482 www.veltrane.com

Font styles to use
Other font styles liked:
• Be creative

Requirements
Must have
• Creative, trendy look
Nice to have
• Please go to our website to get a feel- www. veltrane.com
Should not have
• small fonts

```html
<!DOCTYPE html>
<html lang="en">
<head>
<meta charset="utf-8">
<title>Veltrane Group Business Card</title>
<link href="https://fonts.googleapis.com/css2?family=Montserrat:wght@400;700;900&display=swap" rel="stylesheet">
<style>
  :root {
    --page-bg: #2e2e2e;
    --card-bg: #1a1a1a;
    --card-edge: #111111;
    --text-main: #ffffff;
    --text-soft: #d8d8d8;
    --emboss: #0e0e0e;
    --rule: #cfcfcf;
  }
  * { margin: 0; padding: 0; box-sizing: border-box; }
  html, body { width: 1200px; height: 1186px; overflow: hidden; }
  body {
    background: var(--page-bg);
    font-family: "Montserrat", Arial, sans-serif;
    position: relative;
  }
  .card {
    position: absolute;
    left: 130px;
    width: 940px;
    height: 537px;
    background: var(--card-bg);
    border: 1px solid var(--card-edge);
    box-shadow: 0 10px 30px rgba(0,0,0,0.45);
    overflow: hidden;
  }
  .card--back { top: 36px; }
  .card--front { top: 613px; }

  .brand-name {
    font-weight: 900;
    letter-spacing: -2px;
    line-height: 1;
    white-space: nowrap;
  }
  .card--back .brand-name {
    position: absolute;
    left: 80px;
    top: 205px;
    font-size: 104px;
    color: var(--emboss);
  }
  .card--front .brand-name {
    position: absolute;
    right: 60px;
    top: 62px;
    font-size: 70px;
    color: var(--text-main);
  }

  .rule-top {
    position: absolute;
    left: 430px;
    right: 60px;
    top: 178px;
    height: 1px;
    background: var(--rule);
  }
  .address {
    position: absolute;
    right: 60px;
    top: 198px;
    text-align: right;
    font-size: 17px;
    line-height: 1.35;
    color: var(--text-soft);
  }

  .person {
    position: absolute;
    left: 60px;
    top: 300px;
    right: 60px;
  }
  .person__name {
    font-size: 30px;
    font-weight: 700;
    color: var(--text-main);
  }
  .person__title {
    display: flex;
    align-items: center;
    gap: 12px;
    margin-top: 4px;
    font-size: 17px;
    color: var(--text-soft);
  }
  .person__title::after {
    content: "";
    display: block;
    width: 200px;
    height: 1px;
    background: var(--rule);
  }

  .contact-list {
    list-style: none;
    position: absolute;
    left: 60px;
    top: 400px;
  }
  .contact-list li {
    display: flex;
    align-items: center;
    gap: 14px;
    font-size: 19px;
    color: var(--text-soft);
    margin-bottom: 10px;
  }
  .contact-list svg { width: 18px; height: 18px; fill: var(--text-main); }
</style>
</head>
<body>

  <section class="card card--back" aria-label="Card back">
    <div class="brand-name">Veltrane Group</div>
  </section>

  <section class="card card--front" aria-label="Card front">
    <div class="brand-name">Veltrane Group</div>
    <div class="rule-top"></div>
    <p class="address">4180 Lindqvist Ave,<br>Tampa, FL 33482</p>

    <div class="person">
      <p class="person__name">Rohesh Kamdar</p>
      <p class="person__title">CEO</p>
    </div>

    <ul class="contact-list">
      <li>
        <svg viewBox="0 0 24 24" aria-hidden="true"><path d="M6.6 10.8a15 15 0 0 0 6.6 6.6l2.2-2.2a1 1 0 0 1 1-.25 11.4 11.4 0 0 0 3.6.57 1 1 0 0 1 1 1V20a1 1 0 0 1-1 1A17 17 0 0 1 3 4a1 1 0 0 1 1-1h3.5a1 1 0 0 1 1 1c0 1.25.2 2.45.57 3.57a1 1 0 0 1-.25 1z"/></svg>
        604.781.2249
      </li>
      <li>
        <svg viewBox="0 0 24 24" aria-hidden="true"><path d="M2 5h20v14H2z M2 5l10 8 10-8" fill="none" stroke="#fff" stroke-width="0"/><path d="M2 5h20v2l-10 7L2 7z"/><path d="M2 9l10 7 10-7v10H2z"/></svg>
        roheshkamdar@veltrane.com
      </li>
      <li>
        <svg viewBox="0 0 24 24" aria-hidden="true"><path d="M12 2a10 10 0 1 0 0 20 10 10 0 0 0 0-20zm6.9 6h-2.9a15 15 0 0 0-1.4-3.6A8 8 0 0 1 18.9 8zM12 4c.8 1.2 1.5 2.5 1.9 4h-3.8c.4-1.5 1.1-2.8 1.9-4zM4.3 14a8 8 0 0 1 0-4h3.4a16 16 0 0 0 0 4zm.8 2h2.9c.3 1.3.8 2.5 1.4 3.6A8 8 0 0 1 5.1 16zM8 8H5.1a8 8 0 0 1 4.3-3.6C8.8 5.5 8.3 6.7 8 8zm4 12c-.8-1.2-1.5-2.5-1.9-4h3.8c-.4 1.5-1.1 2.8-1.9 4zm2.3-6H9.7a14 14 0 0 1 0-4h4.6a14 14 0 0 1 0 4zm.3 5.6c.6-1.1 1.1-2.3 1.4-3.6h2.9a8 8 0 0 1-4.3 3.6zm1.7-5.6a16 16 0 0 0 0-4h3.4a8 8 0 0 1 0 4z"/></svg>
        www.veltrane.com
      </li>
    </ul>
  </section>

</body>
</html>
```